Business Card Design Project

Business Card
We are rebranding with a new logo
Industry/Entity Type
Business
Contact Information for Business Card
Dennis Morvale +61 487215963 dennis@quorv.com.au P.O. Box 872 Fernlow QLD 4309
Requirements
Must have
- Logo

```html
<!DOCTYPE html>
<html lang="en">
<head>
<meta charset="utf-8">
<title>Quorv International – Business Card</title>
<link href="https://fonts.googleapis.com/css2?family=Roboto:wght@400;700&family=Damion&display=swap" rel="stylesheet">
<style>
  :root {
    --backdrop: #e4e4e4;
    --card: #f8f8f8;
    --card-edge: #d6d6d6;
    --brand-navy: #17506f;
    --ink: #2a2a2a;
    --accent: #e2692b;
  }
  * { margin: 0; padding: 0; box-sizing: border-box; }
  html, body {
    width: 1200px;
    height: 576px;
    overflow: hidden;
    background: var(--backdrop);
  }
  .sheet {
    position: relative;
    width: 1200px;
    height: 576px;
  }
  .card {
    position: absolute;
    top: 138px;
    width: 484px;
    height: 292px;
    background: var(--card);
    border: 1px solid var(--card-edge);
    border-radius: 12px;
  }
  .card--front { left: 82px; }
  .card--back { left: 602px; }

  .wordmark {
    position: absolute;
    display: flex;
    flex-direction: column;
    align-items: center;
    font-family: "Roboto", sans-serif;
    font-weight: 700;
    color: var(--brand-navy);
    line-height: 1;
  }
  .wordmark__name { letter-spacing: 0.02em; }
  .wordmark__suffix { letter-spacing: 0.16em; }

  .card--front .wordmark {
    left: 0; right: 0;
    top: 96px;
  }
  .card--front .wordmark__name { font-size: 64px; }
  .card--front .wordmark__suffix { font-size: 17px; margin-top: 14px; }

  .card--back .wordmark {
    left: 40px;
    width: 160px;
    top: 104px;
  }
  .card--back .wordmark__name { font-size: 50px; }
  .card--back .wordmark__suffix { font-size: 13px; margin-top: 12px; }

  .contact {
    position: absolute;
    left: 240px;
    top: 94px;
  }
  .contact__name {
    font-family: "Damion", cursive;
    font-size: 27px;
    font-weight: 400;
    color: var(--brand-navy);
    line-height: 1;
    margin-bottom: 20px;
  }
  .contact__list { list-style: none; }
  .contact__item {
    display: flex;
    align-items: center;
    height: 17px;
    font-family: "Roboto", sans-serif;
    font-size: 12.5px;
    color: var(--ink);
  }
  .contact__icon {
    width: 12px;
    height: 12px;
    margin-right: 13px;
    fill: var(--accent);
    flex: none;
  }
</style>
</head>
<body>
<main class="sheet">
  <section class="card card--front" aria-label="Card front">
    <div class="wordmark">
      <span class="wordmark__name">QUORV</span>
      <span class="wordmark__suffix">INTERNATIONAL</span>
    </div>
  </section>

  <section class="card card--back" aria-label="Card back">
    <div class="wordmark">
      <span class="wordmark__name">QUORV</span>
      <span class="wordmark__suffix">INTERNATIONAL</span>
    </div>

    <div class="contact">
      <h1 class="contact__name">Dennis Morvale</h1>
      <ul class="contact__list">
        <li class="contact__item">
          <svg class="contact__icon" viewBox="0 0 24 24" aria-hidden="true">
            <path d="M2 8c0-3 4-5 10-5s10 2 10 5v2h-5V8c-1-1-3-1.5-5-1.5S8 7 7 8v2H2z"/>
            <path d="M5 11h14l2 10H3z"/>
          </svg>
          +61 487215963
        </li>
        <li class="contact__item">
          <svg class="contact__icon" viewBox="0 0 24 24" aria-hidden="true">
            <path d="M2 5h20v14H2z M4 7v1l8 5 8-5V7l-8 5z" fill-rule="evenodd"/>
          </svg>
          dennis@quorv.com.au
        </li>
        <li class="contact__item">
          <svg class="contact__icon" viewBox="0 0 24 24" aria-hidden="true">
            <path d="M12 1a8 8 0 0 0-8 8c0 6 8 14 8 14s8-8 8-14a8 8 0 0 0-8-8zm0 11a3 3 0 1 1 0-6 3 3 0 0 1 0 6z"/>
          </svg>
          P.O. Box 872 Fernlow QLD 4309
        </li>
      </ul>
    </div>
  </section>
</main>
</body>
</html>
```